Business Card Design

I'm a commercial general contractor remodel offices, hotels, health clubs and stores mostly San Francisco and the peninsula
the file I down loaded is kind of what I want I like the I beam with my company name in it, that would be fine with me but if you have better Idea will look at it you never know, I'm decided to give in and change my company name to how every one knows me, I have been in business since 1991, I like the I beam logo I included one of my old card from my old company for reference for you.

BROCK CONSTRUCTION (is my company name)
Warren Pelkey contractor, LIc 514387
3148 Larkspur Row, San Bruno, California 94071
mobile, (415) 736-4052
phone (650) 514-2087
Fax, (650) 514-2088
email, brock@brockconstruction.example

```html
<!DOCTYPE html>
<html lang="en">
<head>
<meta charset="utf-8">
<title>Brock Construction – Business Card</title>
<link rel="stylesheet" href="https://fonts.googleapis.com/css2?family=Source+Sans+3:wght@300;400;600&display=swap">
<style>
  :root {
    --page-bg: #e9e6e1;
    --card-white: #ffffff;
    --card-white-shade: #eeeeee;
    --band-dark: #2a2a2a;
    --band-mid: #464646;
    --accent-blue: #5a9ad6;
    --name-blue: #6aa6dd;
    --text-light: #f2f2f2;
    --text-soft: #d6d6d6;
    --divider: #6a6a6a;
  }
  html, body {
    margin: 0;
    padding: 0;
    width: 1200px;
    height: 1023px;
    overflow: hidden;
    background: var(--page-bg);
    font-family: "Source Sans 3", "Myriad Pro", Arial, sans-serif;
  }
  .business-card {
    position: absolute;
    left: 100px;
    top: 226px;
    width: 1000px;
    height: 571px;
    border-radius: 6px;
    overflow: hidden;
    box-shadow: 0 18px 40px rgba(0,0,0,0.25);
  }
  .card-backdrop {
    position: absolute;
    inset: 0;
    width: 100%;
    height: 100%;
  }
  .brand {
    position: absolute;
    left: 70px;
    top: 160px;
    display: flex;
    align-items: center;
    gap: 14px;
    white-space: nowrap;
  }
  .brand-mark {
    width: 22px;
    height: 22px;
    background: var(--accent-blue);
  }
  .brand-name {
    font-size: 28px;
    line-height: 34px;
    font-weight: 600;
    letter-spacing: 2px;
    color: var(--accent-blue);
  }
  .holder-name {
    position: absolute;
    left: 70px;
    top: 378px;
    margin: 0;
    font-size: 40px;
    font-weight: 300;
    letter-spacing: 1px;
    text-transform: uppercase;
    color: var(--name-blue);
    white-space: nowrap;
  }
  .contact-list {
    position: absolute;
    list-style: none;
    margin: 0;
    padding: 0;
  }
  .contact-list li {
    display: flex;
    align-items: center;
    gap: 16px;
    color: var(--text-soft);
    white-space: nowrap;
  }
  .contact-list svg {
    width: 26px;
    height: 26px;
    flex: none;
  }
  .contact-list--left {
    left: 70px;
    top: 446px;
  }
  .contact-list--left li {
    font-size: 22px;
    line-height: 27px;
    margin-bottom: 14px;
  }
  .address-line { display: block; }
  .divider {
    position: absolute;
    left: 610px;
    top: 280px;
    width: 1px;
    height: 200px;
    background: var(--divider);
  }
  .role-title {
    position: absolute;
    left: 650px;
    top: 222px;
    margin: 0;
    font-size: 30px;
    font-weight: 400;
    letter-spacing: 1px;
    color: var(--text-light);
  }
  .contact-list--right {
    left: 650px;
    top: 290px;
  }
  .contact-list--right li {
    font-size: 26px;
    margin-bottom: 22px;
    color: var(--text-light);
  }
</style>
</head>
<body>
  <article class="business-card">
    <svg class="card-backdrop" viewBox="0 0 1000 571" preserveAspectRatio="none" aria-hidden="true">
      <defs>
        <linearGradient id="whiteFace" x1="0" y1="0" x2="1" y2="1">
          <stop offset="0" stop-color="var(--card-white)"/>
          <stop offset="1" stop-color="var(--card-white-shade)"/>
        </linearGradient>
        <linearGradient id="darkBand" x1="0" y1="1" x2="1" y2="0">
          <stop offset="0" stop-color="var(--band-dark)"/>
          <stop offset="0.55" stop-color="var(--band-mid)"/>
          <stop offset="1" stop-color="var(--band-dark)"/>
        </linearGradient>
      </defs>
      <rect width="1000" height="571" fill="url(#whiteFace)"/>
      <polygon points="0,358 1000,108 1000,571 0,571" fill="url(#darkBand)"/>
      <line x1="0" y1="346" x2="1000" y2="96" stroke="var(--accent-blue)" stroke-width="4"/>
    </svg>

    <div class="brand">
      <span class="brand-mark"></span>
      <span class="brand-name">BROCK CONSTRUCTION</span>
    </div>

    <h1 class="holder-name">Warren Pelkey</h1>

    <ul class="contact-list contact-list--left">
      <li>
        <svg viewBox="0 0 26 26" aria-hidden="true"><circle cx="13" cy="13" r="11.5" fill="none" stroke="var(--accent-blue)" stroke-width="1.6"/><rect x="7" y="9" width="12" height="8" fill="none" stroke="var(--accent-blue)" stroke-width="1.4"/><polyline points="7,9 13,14 19,9" fill="none" stroke="var(--accent-blue)" stroke-width="1.4"/></svg>
        <span>brock@brockconstruction.example</span>
      </li>
      <li>
        <svg viewBox="0 0 26 26" aria-hidden="true"><path d="M13 24 C7 16 5 13 5 10 a8 8 0 0 1 16 0 c0 3 -2 6 -8 14z" fill="none" stroke="var(--accent-blue)" stroke-width="1.8"/><circle cx="13" cy="10" r="3" fill="var(--accent-blue)"/></svg>
        <span>
          <span class="address-line">Llc 514387, 3148 Larkspur Row</span>
          <span class="address-line">San Bruno, California 94071</span>
        </span>
      </li>
    </ul>

    <div class="divider"></div>

    <h2 class="role-title">CONTRACTOR</h2>

    <ul class="contact-list contact-list--right">
      <li>
        <svg viewBox="0 0 26 26" aria-hidden="true"><rect x="7" y="2" width="12" height="22" rx="2" fill="var(--accent-blue)"/><rect x="9" y="5" width="8" height="13" fill="var(--band-dark)"/><circle cx="13" cy="21" r="1.3" fill="var(--band-dark)"/></svg>
        <span>(415) 736-4052</span>
      </li>
      <li>
        <svg viewBox="0 0 26 26" aria-hidden="true"><circle cx="13" cy="13" r="12" fill="var(--accent-blue)"/><path d="M8 7 l3 -1 2 4 -2 1.5 c1 2 2 3 4 4 l1.5 -2 4 2 -1 3 c-6 0 -11.5 -5.5 -11.5 -11.5z" fill="var(--band-dark)"/></svg>
        <span>(650) 514-2087</span>
      </li>
      <li>
        <svg viewBox="0 0 26 26" aria-hidden="true"><rect x="3" y="3" width="20" height="20" rx="2" fill="none" stroke="var(--accent-blue)" stroke-width="1.8"/><rect x="7" y="7" width="8" height="4" fill="var(--accent-blue)"/><rect x="7" y="14" width="12" height="2" fill="var(--accent-blue)"/><rect x="7" y="18" width="12" height="2" fill="var(--accent-blue)"/></svg>
        <span>(650) 514-2088</span>
      </li>
    </ul>
  </article>
</body>
</html>
```